IT Company requires new Business Card design.

Over the years we have had a few different business card designs. We are now due for new cards across the board for all staff. We felt this would be a good time to start fresh with a new design. Our traditional card simply had our details on the front, and a list of services on the back. We don't particularly need the list of services, we have had cards where the only thing on the rear of the card was our logo.
Feel free to be creative, we would like our tag line "Complete IT Management" to appear at some point, doesn't necessarily have to be with the logo.
I have attached samples and drafts of various previous cards we have used over the years.

```html
<!DOCTYPE html>
<html lang="en">
<head>
<meta charset="utf-8">
<title>Ridgeway Networking – Business Card</title>
<link href="https://fonts.googleapis.com/css2?family=Open+Sans:wght@400;700&display=swap" rel="stylesheet">
<style>
  :root {
    --backdrop: #e9e9ee;
    --card: #ffffff;
    --slate: #5f7282;
    --ink: #3c3f44;
    --edge: #d3d5da;
  }
  * { box-sizing: border-box; margin: 0; padding: 0; }
  html, body { width: 1200px; height: 987px; overflow: hidden; }
  body {
    background: var(--backdrop);
    font-family: "Open Sans", Arial, sans-serif;
    position: relative;
  }
  .card {
    position: absolute;
    width: 740px;
    height: 423px;
    background: var(--card);
    border-radius: 34px;
    border: 1px solid var(--edge);
    box-shadow: 0 6px 18px rgba(0,0,0,0.08);
  }
  .card--back { left: 400px; top: 50px; }
  .card--front { left: 60px; top: 510px; }

  /* Back */
  .back-brand {
    position: absolute;
    left: 0; right: 0; top: 120px;
    text-align: center;
    color: var(--slate);
    font-weight: 700;
    font-size: 58px;
    line-height: 1.05;
    letter-spacing: 1px;
    text-transform: uppercase;
  }
  .back-web {
    position: absolute;
    left: 0; right: 0; bottom: 58px;
    text-align: center;
    color: var(--ink);
    font-size: 22px;
    letter-spacing: 2px;
  }

  /* Front */
  .accent-bar {
    position: absolute;
    left: 0; top: 34px;
    width: 16px; height: 40px;
    background: var(--slate);
  }
  .details { position: absolute; left: 40px; top: 32px; color: var(--ink); }
  .person-name { color: var(--slate); font-weight: 700; font-size: 22px; line-height: 1.2; }
  .person-role { font-size: 17px; margin-bottom: 16px; }
  .address { font-size: 17px; line-height: 1.3; margin-bottom: 14px; }
  .contact-list { list-style: none; font-size: 17px; line-height: 1.45; }
  .contact-list li { display: flex; align-items: center; gap: 8px; }
  .contact-list svg { width: 14px; height: 14px; fill: var(--slate); flex: none; }
  .tagline {
    position: absolute; left: 40px; bottom: 34px;
    color: var(--slate); font-weight: 700; font-size: 18px;
  }
  .front-brand {
    position: absolute;
    right: 52px; top: 150px;
    display: flex; align-items: center; gap: 16px;
    color: var(--slate);
    font-weight: 700;
    font-size: 40px;
    line-height: 1.02;
    text-transform: uppercase;
  }
  .brand-square { width: 54px; height: 54px; background: var(--slate); flex: none; }
</style>
</head>
<body>

<section class="card card--back" aria-label="Card back">
  <div class="back-brand">Ridgeway<br>Networking</div>
  <div class="back-web">www.ridgewaynet.com.au</div>
</section>

<section class="card card--front" aria-label="Card front">
  <div class="accent-bar"></div>
  <div class="details">
    <div class="person-name">Daniel Hart</div>
    <div class="person-role">Operation Manager</div>
    <div class="address">Unit 7 22 Harlow Street<br>Bibra Lake WA 6163</div>
    <ul class="contact-list">
      <li><svg viewBox="0 0 16 16"><circle cx="8" cy="8" r="7.5" fill="none" stroke="currentColor"/><path d="M5 4l2 2-1 1 3 3 1-1 2 2-1.5 1.5C7 12 4 9 3.5 5.5z"/></svg>08 9300 4410</li>
      <li><svg viewBox="0 0 16 16"><rect x="4" y="1" width="8" height="14" rx="1.5"/><rect x="5.5" y="3" width="5" height="5" fill="#fff"/></svg>0412 880 617</li>
      <li><svg viewBox="0 0 16 16"><rect x="4" y="2" width="8" height="4"/><rect x="1" y="6" width="14" height="6" rx="1"/><rect x="4" y="10" width="8" height="4"/></svg>08 9300 4410</li>
      <li><svg viewBox="0 0 16 16"><rect x="1" y="3" width="14" height="10" rx="1"/><path d="M1.5 3.5L8 9l6.5-5.5" fill="none" stroke="#fff" stroke-width="1.3"/></svg>daniel@ridgewaynet.com.au</li>
      <li><svg viewBox="0 0 16 16"><circle cx="8" cy="8" r="7"/><path d="M1 8h14M8 1c-3 3-3 11 0 14M8 1c3 3 3 11 0 14" fill="none" stroke="#fff"/></svg>www.ridgewaynet.com.au</li>
    </ul>
  </div>
  <div class="tagline">Complete IT Management</div>
  <div class="front-brand">
    <span class="brand-square"></span>
    <span>Ridgeway<br>Networking</span>
  </div>
</section>

</body>
</html>
```